Veltra Metrics New Website for Health Benefits Plan Decisioneering Tool Launch

Veltra Metrics is a SaaS provider of health benefits comparison tools. We need a new simple SaaS focused website to direct customers to our product

Target Market(s)

General Public comparing their health benefits plans from their employer or from the state exchanges in the US

Coding

Coded - Design and coding required

Number of Pages Required

3 page

Requirements
Must have
• Main page - "Know the Best Health Benefits Plan for You!"
Graphic of a person looking over papers on their desk
Compare Now button to link to SaaS product
About Us
Product Page

https://plimbo.example/top-app-pages/

```html
<!DOCTYPE html>
<html lang="en">
<head>
<meta charset="utf-8">
<title>Veltra Metrics – Health Benefits Plan Comparison</title>
<link rel="stylesheet" href="https://fonts.googleapis.com/css2?family=Cinzel:wght@400;700&family=Mulish:wght@400;500;600&display=swap">
<style>
  :root {
    --brand-blue: #29a8df;
    --hero-blue: #79b8d2;
    --hero-deep: #5f9fbc;
    --ink: #2b2b2b;
    --body-text: #444444;
    --white: #ffffff;
    --footer-bg: #333333;
    --social-tint: #5a5a5a;
  }
  * { box-sizing: border-box; margin: 0; padding: 0; }
  html, body { width: 1200px; height: 1078px; overflow: hidden; background: var(--white); }
  body { position: relative; font-family: "Mulish", Arial, sans-serif; color: var(--body-text); }

  .site-header { position: absolute; top: 0; left: 0; width: 1200px; height: 96px; }
  .brand { position: absolute; left: 141px; top: 22px; font-family: "Cinzel", serif; color: var(--brand-blue); font-weight: 400; text-align: center; width: 256px; line-height: 1; }
  .brand-name { display: block; font-size: 29px; letter-spacing: 0.5px; }
  .brand-suffix { display: block; font-size: 17px; letter-spacing: 3px; margin-top: 6px; }

  .main-nav { position: absolute; top: 25px; right: 141px; display: flex; align-items: center; height: 39px; }
  .main-nav a { text-decoration: none; color: var(--ink); font-size: 13px; font-weight: 500; letter-spacing: 0.6px; margin-right: 34px; }
  .main-nav a.nav-contact { margin-right: 0; background: var(--brand-blue); color: var(--white); width: 135px; height: 39px; display: flex; align-items: center; justify-content: center; border-radius: 2px; margin-left: 0; }

  .hero { position: absolute; top: 96px; left: 0; width: 1200px; height: 542px; background: var(--hero-blue); }
  .hero-illustration { position: absolute; left: 88px; top: 49px; width: 526px; height: 462px; border-radius: 6px; background: radial-gradient(ellipse at 50% 55%, #8fc4da 0%, var(--hero-blue) 75%); }
  .hero-copy { position: absolute; left: 654px; top: 160px; }
  .hero-title { font-family: "Cinzel", serif; font-weight: 700; color: var(--white); font-size: 45px; line-height: 51px; letter-spacing: 0.5px; }
  .btn-compare { display: flex; align-items: center; justify-content: center; margin-top: 26px; width: 162px; height: 42px; background: var(--white); color: var(--brand-blue); text-decoration: none; font-size: 14px; font-weight: 600; letter-spacing: 0.8px; border-radius: 2px; }

  .about { position: absolute; top: 638px; left: 0; width: 1200px; height: 394px; text-align: center; }
  .about-title { margin-top: 59px; font-family: "Cinzel", serif; font-weight: 400; color: var(--brand-blue); font-size: 33px; letter-spacing: 0.5px; line-height: 1; }
  .about-rule { position: relative; width: 397px; height: 24px; margin: 5px auto 0; }
  .about-rule::before, .about-rule::after { content: ""; position: absolute; top: 12px; width: 169px; height: 2px; background: var(--brand-blue); }
  .about-rule::before { left: 0; }
  .about-rule::after { right: 0; }
  .about-rule span { font-family: "Cinzel", serif; color: var(--brand-blue); font-size: 20px; line-height: 24px; }
  .about-text { width: 880px; margin: 12px auto 0; font-size: 14px; line-height: 27px; color: var(--body-text); }
  .btn-read { display: inline-flex; align-items: center; justify-content: center; margin-top: 22px; width: 127px; height: 39px; background: var(--brand-blue); color: var(--white); text-decoration: none; font-size: 13px; font-weight: 600; letter-spacing: 0.6px; border-radius: 2px; }

  .site-footer { position: absolute; top: 1032px; left: 0; width: 1200px; height: 46px; background: var(--footer-bg); }
  .copyright { position: absolute; left: 143px; top: 0; line-height: 46px; color: #e6e6e6; font-size: 13px; }
  .copyright strong { font-family: "Cinzel", serif; font-weight: 400; font-size: 14px; }
  .social { position: absolute; right: 141px; top: 9px; display: flex; gap: 7px; }
  .social a { display: block; width: 28px; height: 28px; border-radius: 50%; background: var(--social-tint); border: 1px solid #777; }
</style>
</head>
<body>
  <header class="site-header">
    <div class="brand"><span class="brand-name">VELTRA METRICS</span><span class="brand-suffix">LLC</span></div>
    <nav class="main-nav">
      <a href="#home">HOME</a>
      <a href="#about">ABOUT US</a>
      <a href="#product">PRODUCT</a>
      <a class="nav-contact" href="#contact">CONTACT US</a>
    </nav>
  </header>

  <section class="hero" id="home">
    <div class="hero-illustration" role="img" aria-label="Illustration of a person at a desk looking over papers, folders and a computer showing charts"></div>
    <div class="hero-copy">
      <h1 class="hero-title">KNOW THE BEST<br>HEALTH BENEFITS<br>PLAN FOR YOU!</h1>
      <a class="btn-compare" href="#product">COMPARE NOW</a>
    </div>
  </section>

  <section class="about" id="about">
    <h2 class="about-title">ABOUT VELTRA METRICS</h2>
    <div class="about-rule"><span>LLC</span></div>
    <p class="about-text">Lorem ipsum dolor sit amet, consectetuer adipiscing elit, sed diam nonummy nibh euismod tincidunt ut laoreet dolore magna aliquam erat volutpat. Ut wisi enim ad minim veniam, quis nostrud exerci tation ullamcorper suscipit lobortis nisl ut aliquip ex ea commodo consequat. Duis autem vel eum iriure dolor in hendrerit in vulputate velit esse molestie consequat, vel illum dolore eu feugiat nulla facilisis at vero eros et accumsan et iusto odio dignissim qui blandit praesent luptatum zzril delenit augue duis dolore te feugait nulla facilisi exerci tation ullamcorper suscipit lobortis dolor in hendrerit in vulputate velit esse molestie.</p>
    <a class="btn-read" href="#about">READ MORE</a>
  </section>

  <footer class="site-footer">
    <p class="copyright">Copyright © 2020 <strong>VELTRA METRICS LLC.</strong> All Rights Reserved.</p>
    <div class="social">
      <a href="#" aria-label="Social profile one"></a>
      <a href="#" aria-label="Social profile two"></a>
      <a href="#" aria-label="Social profile three"></a>
      <a href="#" aria-label="Video channel"></a>
    </div>
  </footer>
</body>
</html>
```